AUTOMOTIVE/ CAR REPAIRS / CRASH REPAIRS / PAINT SPRAYING AND PANEL BEATING

AUTOMOTIVE REPAIR. CAR / MOTORCYCLES GOT LOGO DESIGN / DID THINK ABOUT FACELANE DONT NOALREADY HAVE WEB ADRESS www.brenvashine.co.uk and mail sales@brenvashine,co.uk NEED SOMETHINK I CAN MANAGE TO UPLOAD PICTURES IN TO A GALLERY OR SOMETHINGLIKE THAT I ALSO SELL CAR AND MOTORCYCLES MAYBE A SELLS PAGE WITH A TILLWAVE LINK

Target Market(s)

TRADE / GENERAL PUBLIC

Industry/Entity Type

Automotive

Coding

Coded - Design and coding required

Number of Pages Required

4 page

Font styles to use
Serif
Sans Serif

Colors

Designer to choose colors to be used in the design.

Requirements
Must have
• GALLERY/ SHOP TO SALE CARS AND MOTORCYCLE / LOGOS OF MATERIALS I USE DORFLINT / KEBO / VASTINCO / Q WRAP / GLENBRUSH
• CONTACT US
Nice to have
• TILLWAVE / EASY TO MANAGE / VIDEO CLIP OF DORFLINT HUE PLANNER Z7
• SWIFT BLEND PAINT TONVIEW WETLINE AND TULVOKE

```html
<!DOCTYPE html>
<html lang="en">
<head>
<meta charset="utf-8">
<title>Brenvashine Bodyshop</title>
<link href="https://fonts.googleapis.com/css2?family=Lato:ital,wght@0,400;0,700;0,900;1,700;1,900&display=swap" rel="stylesheet">
<style>
:root{
  --navy:#161a26;
  --navy-2:#1d2231;
  --red:#c8101a;
  --red-dark:#7a0710;
  --red-bright:#e11d24;
  --grey-bg:#f1f1f1;
  --text:#222;
  --muted:#555;
  --white:#fff;
}
*{box-sizing:border-box;margin:0;padding:0}
html,body{width:1200px;height:4119px;overflow:hidden}
body{font-family:'Lato',sans-serif;color:var(--text);background:var(--white);position:relative}
.abs{position:absolute}
.photo{position:absolute}

/* header */
.site-header{position:absolute;left:0;top:0;width:1200px;height:105px;background:var(--navy)}
.brand{position:absolute;left:80px;top:28px;color:var(--white);display:flex;align-items:center;gap:10px}
.brand-dot{width:16px;height:16px;border-radius:50%;background:var(--red-bright)}
.brand-name{font-weight:900;font-size:26px;letter-spacing:2px}
.brand-sub{position:absolute;left:80px;top:64px;color:#ccc;font-size:12px;letter-spacing:8px;width:260px;text-align:center}
.nav{position:absolute;left:393px;top:34px;display:flex;align-items:center;gap:0}
.nav a{color:var(--white);font-size:14px;font-weight:700;text-decoration:none;height:36px;line-height:36px;padding:0 22px;margin-right:14px}
.nav a.active{background:var(--red-bright);border-radius:18px}
.cart{color:var(--white);font-size:13px;font-weight:700;margin-left:6px;display:flex;align-items:center;gap:4px}
.cart-count{background:var(--red-bright);border-radius:50%;width:13px;height:13px;font-size:9px;text-align:center;line-height:13px}

/* hero */
.hero-photo{left:0;top:105px;width:1200px;height:640px;background:linear-gradient(160deg,#5a5a5e 0%,#3d3d42 35%,#8a1a1d 60%,#5a5a5e 100%)}
.hero-title{position:absolute;left:0;width:1200px;text-align:center;color:var(--white)}
.hero-title h1{position:absolute;top:205px;width:100%;font-weight:900;font-style:italic;font-size:112px;letter-spacing:-2px}
.hero-title .line1{position:absolute;top:322px;width:100%;font-size:40px;font-weight:700}
.hero-title .line2{position:absolute;top:360px;width:100%;font-size:31px;font-weight:700}
.btn-dark{position:absolute;background:#0d0f15;color:var(--white);font-size:14px;font-weight:700;border-radius:22px;text-align:center}
.hero-dots{position:absolute;top:560px;left:560px;display:flex;gap:11px}
.hero-dots span{width:11px;height:11px;border-radius:50%;background:var(--white)}

/* about */
.about-card{position:absolute;left:75px;top:760px;width:1051px;height:410px;background:var(--grey-bg)}
.section-title{font-weight:900;font-style:italic;font-size:38px;text-align:center}
.about-card .section-title{position:absolute;top:32px;width:100%}
.title-rule{position:absolute;top:98px;left:358px;width:335px;height:1px;background:#aaa}
.title-rule::after{content:"";position:absolute;left:158px;top:-10px;width:20px;height:20px;border-radius:50%;background:var(--red);border:3px solid var(--grey-bg)}
.about-kicker{position:absolute;left:23px;top:135px;color:var(--red);font-weight:900;font-style:italic;font-size:23px}
.about-lead{position:absolute;left:23px;top:173px;width:510px;font-size:16px;font-weight:700;line-height:25px}
.about-body{position:absolute;left:23px;top:225px;width:510px;font-size:14px;line-height:25px;color:#333}
.about-photo{left:565px;top:120px;width:486px;height:290px;background:radial-gradient(ellipse at 55% 55%,#d11a22 0%,#a5121a 40%,#e8e8e8 72%)}

/* what we do */
.services-title{position:absolute;top:1272px;width:1200px;color:var(--white)}
.services-sub{position:absolute;top:1338px;width:1200px;text-align:center;color:var(--white);font-size:16px}
.service-card{position:absolute;top:1402px;width:242px;height:353px;background:var(--grey-bg);border-radius:6px;text-align:center}
.service-card .photo{left:12px;top:10px;width:218px;height:164px;border-radius:4px}
.service-card h3{position:absolute;top:193px;width:100%;color:var(--red);font-weight:900;font-size:22px;line-height:27px}
.service-card p{position:absolute;top:253px;left:18px;width:206px;font-size:14px;line-height:25px;color:#333}
.arrow{position:absolute;top:1565px}

/* customisation */
.custom-photo{left:30px;top:2000px;width:530px;height:190px;background:radial-gradient(ellipse at 50% 55%,#e0151e 0%,#a10e16 50%,rgba(80,10,14,0) 75%)}
.custom-title{position:absolute;left:593px;top:1988px;color:var(--white);font-weight:900;font-style:italic;font-size:38px}
.custom-text{position:absolute;left:593px;top:2051px;width:540px;color:#eee;font-size:16px;line-height:27px}
.custom-strong{position:absolute;left:593px;top:2114px;width:520px;color:var(--white);font-size:17px;font-weight:900;line-height:27px}

/* gallery */
.gallery-title{position:absolute;top:2355px;width:1200px}
.gal{border-radius:8px}

/* partners */
.partners{position:absolute;top:3020px;left:0;width:1200px;display:flex;justify-content:space-around;padding:0 90px}
.partner{display:flex;align-items:center;gap:8px;font-weight:900;font-size:28px;color:var(--navy)}
.partner-sq{width:18px;height:18px;background:var(--red)}

/* contact */
.contact-title{position:absolute;left:75px;top:3222px;color:var(--white);font-weight:900;font-style:italic;font-size:38px}
.contact-lead{position:absolute;left:75px;top:3290px;width:470px;color:var(--white);font-size:17px;font-weight:900;line-height:26px}
.contact-line{position:absolute;left:75px;color:var(--white);font-size:16px;line-height:26px;display:flex;gap:16px}
.icon{flex:none;margin-top:5px}
.field{position:absolute;background:var(--white);border-radius:20px;font-size:12px;color:#333;padding:0 20px;line-height:38px}
.field.message{border-radius:14px;line-height:20px;padding-top:12px}
.btn-red{position:absolute;left:75px;top:3685px;width:154px;height:42px;border-radius:21px;background:linear-gradient(180deg,#e11d24,#b00d14);color:var(--white);font-weight:700;font-size:14px;text-align:center;line-height:42px}
.map{left:587px;top:3233px;width:539px;height:497px;background:linear-gradient(135deg,#eceef0 0%,#e4e6e9 60%,#c9e6bd 75%,#e4e6e9 90%)}

/* footer */
.footer-brand{position:absolute;left:75px;top:3925px;display:flex;align-items:center;gap:8px;color:var(--navy)}
.footer-brand .brand-name{font-size:24px}
.footer-sub{position:absolute;left:75px;top:3958px;width:240px;text-align:center;font-size:12px;letter-spacing:7px;color:#333}
.footer-copy{position:absolute;left:75px;top:3988px;font-size:12px;line-height:18px;color:#333}
.socials{position:absolute;left:75px;top:4042px;display:flex;gap:14px;font-size:12px;font-weight:700;color:#333}
.footer-col{position:absolute;top:3925px;font-size:14px;line-height:27px;color:#333}
.footer-col h4{font-size:16px;font-weight:900;color:#222;line-height:22px;margin-bottom:4px}
.badge{position:absolute;left:912px;top:3918px;width:130px;height:110px;border-radius:50%;background:radial-gradient(circle,#e0b23a 0%,#a87a12 70%)}
.pay{position:absolute;left:952px;top:4043px;display:flex;align-items:center;gap:6px;font-size:13px;font-weight:900;color:#1b3b8a}
.pay-sq{width:12px;height:12px;background:#1b3b8a}
.footer-car{left:1010px;top:3850px;width:190px;height:110px;background:radial-gradient(ellipse at 60% 60%,#d7141d 0%,#9d0e15 45%,rgba(255,255,255,0) 72%)}
</style>
</head>
<body>

<header class="site-header">
  <div class="brand"><span class="brand-name">BRENVASHINE</span><span class="brand-dot"></span></div>
  <div class="brand-sub">BODYSHOP</div>
  <nav class="nav">
    <a class="active">HOME</a><a>ABOUT US</a><a>SERVICE</a><a>CUSTOM</a><a>GALLERY</a><a>CONTACT</a>
    <span class="cart">
      <svg width="12" height="12" viewBox="0 0 12 12"><path d="M0 1h2l2 7h6l1.5-5H3" fill="none" stroke="#fff" stroke-width="1.5"/><circle cx="4.5" cy="10.5" r="1" fill="#fff"/><circle cx="9.5" cy="10.5" r="1" fill="#fff"/></svg>
      <span class="cart-count">0</span>
    </span>
  </nav>
</header>

<!-- hero -->
<div class="photo hero-photo" role="img" aria-label="Workshop photo of a red classic car being restored"></div>
<svg class="abs" style="left:0;top:600px" width="1200" height="250" viewBox="0 0 1200 250">
  <defs><linearGradient id="heroWave" x1="0" x2="1"><stop offset="0" stop-color="#8e0a12"/><stop offset=".5" stop-color="#e0151e"/><stop offset="1" stop-color="#8e0a12"/></linearGradient></defs>
  <path d="M0 80 C250 -10 400 120 700 90 C950 60 1080 20 1200 70 L1200 245 L0 245 Z" fill="url(#heroWave)"/>
  <rect x="0" y="245" width="1200" height="5" fill="#fff"/>
</svg>
<div class="hero-title">
  <h1>BRENVASHINE</h1>
  <div class="line1">YOUR ONE STOP BODY SHOP</div>
  <div class="line2">The home of paint perfection</div>
</div>
<div class="btn-dark" style="left:524px;top:422px;width:154px;height:42px;line-height:42px">CONTACT US</div>
<div class="hero-dots"><span></span><span></span><span></span><span></span></div>

<!-- about -->
<section class="about-card">
  <h2 class="section-title">ABOUT BRENVASHINE</h2>
  <div class="title-rule"></div>
  <div class="about-kicker">YOUR ONE STOP BODYSHOP</div>
  <p class="about-lead">Fully qualified trained technicians family run business established over 30 years.</p>
  <p class="about-body" style="top:226px">Brenvashine, based in Elmbridge, Westshire established in August, 1985 has grown to become Westshire's premiere manufacturer approved accident repair centre.</p>
  <div class="btn-dark" style="left:23px;top:320px;width:154px;height:45px;line-height:45px">READ MORE</div>
  <div class="photo about-photo" role="img" aria-label="Red sports car front view"></div>
</section>

<!-- what we do -->
<svg class="abs" style="left:0;top:1230px" width="1200" height="560" viewBox="0 0 1200 560">
  <defs><linearGradient id="svcBg" x1="0" x2="1"><stop offset="0" stop-color="#a50b14"/><stop offset=".5" stop-color="#5a0a12"/><stop offset="1" stop-color="#161a26"/></linearGradient></defs>
  <path d="M0 0 H1200 V270 C900 220 600 330 300 300 C160 285 60 290 0 290 Z" fill="url(#svcBg)"/>
</svg>
<h2 class="section-title services-title">WHAT WE DO</h2>
<p class="services-sub">From the repair of the smallest dents and scratches to major auto repair work, Brenvashine is set up to meet your needs.</p>

<article class="service-card" style="left:75px">
  <div class="photo" role="img" aria-label="Damaged car front awaiting body repair" style="background:linear-gradient(160deg,#8c8c8c,#4a4a4a)"></div>
  <h3>CAR<br>BODY REPAIRS</h3>
  <p>Duis est turpis, cursus a sollicitudin ac, auctor ornare magna sed dictum.</p>
</article>
<article class="service-card" style="left:345px">
  <div class="photo" role="img" aria-label="Painter spraying a motorcycle part in a booth" style="background:linear-gradient(160deg,#a9a9a9,#5c5c5c 60%,#9a1a1e)"></div>
  <h3>MOTORCYCLE<br>PAINTING</h3>
  <p>Duis est turpis, cursus a sollicitudin ac, auctor ornare magna sed dictum.</p>
</article>
<article class="service-card" style="left:615px">
  <div class="photo" role="img" aria-label="Alloy wheel being spray painted" style="background:linear-gradient(160deg,#b8b8b8,#555)"></div>
  <h3>WHEEL<br>PAINTING</h3>
  <p>Duis est turpis, cursus a sollicitudin ac, auctor ornare magna sed dictum.</p>
</article>
<article class="service-card" style="left:885px">
  <div class="photo" role="img" aria-label="Mechanic working on a red car engine bay" style="background:linear-gradient(160deg,#6a1216,#c4141c 55%,#3a3a3a)"></div>
  <h3>IE CARS &amp;<br>BIKES</h3>
  <p>Duis est turpis, cursus a sollicitudin ac, auctor ornare magna sed dictum.</p>
</article>
<svg class="arrow" style="left:44px" width="16" height="26" viewBox="0 0 16 26"><path d="M13 2 L3 13 L13 24" fill="none" stroke="#333" stroke-width="3"/></svg>
<svg class="arrow" style="left:1140px" width="16" height="26" viewBox="0 0 16 26"><path d="M3 2 L13 13 L3 24" fill="none" stroke="#333" stroke-width="3"/></svg>

<!-- customisation -->
<svg class="abs" style="left:0;top:1815px" width="1200" height="500" viewBox="0 0 1200 500">
  <defs><linearGradient id="custBg" x1="0" x2="1" y1="0" y2="1"><stop offset="0" stop-color="#2a0d12"/><stop offset=".45" stop-color="#7d0c14"/><stop offset="1" stop-color="#3a0a10"/></linearGradient></defs>
  <path d="M0 40 C150 10 300 0 500 30 C700 60 800 90 1000 70 C1100 60 1160 50 1200 45 V500 H0 Z" fill="url(#custBg)"/>
</svg>
<div class="photo custom-photo" role="img" aria-label="Red supercar side view"></div>
<h2 class="custom-title">CUSTOMISATION</h2>
<p class="custom-text">Our experienced team can efficiently carry out any customising work you require in order to meet the specific design you have in mind.</p>
<p class="custom-strong" style="top:2115px">BRENVASHINE CAN ENHANCE YOUR CAR TO SUIT YOUR PERSONAL TASTE</p>
<div class="btn-dark" style="left:593px;top:2199px;width:154px;height:42px;line-height:42px;background:#1a0f14">READ MORE</div>

<!-- gallery -->
<h2 class="section-title gallery-title">GALLERY</h2>
<div class="photo gal" role="img" aria-label="Blue car masked for paint" style="left:75px;top:2432px;width:339px;height:254px;background:linear-gradient(150deg,#cfd3da,#2c3a6a 55%,#1e2a52)"></div>
<div class="photo gal" role="img" aria-label="Mechanic servicing a motorcycle" style="left:431px;top:2432px;width:339px;height:254px;background:linear-gradient(150deg,#6d6d6d,#1f1f1f 60%,#8a3a18)"></div>
<div class="photo gal" role="img" aria-label="Red classic convertible in workshop" style="left:786px;top:2432px;width:340px;height:254px;background:linear-gradient(170deg,#b9b2a8,#b3141c 55%,#7d7a76)"></div>
<div class="photo gal" role="img" aria-label="Silver convertible sports car" style="left:75px;top:2705px;width:695px;height:253px;background:linear-gradient(170deg,#d9d9d9,#a8a8a8 55%,#6c6c6c)"></div>
<div class="photo gal" role="img" aria-label="Technician repairing a sports motorcycle" style="left:786px;top:2705px;width:340px;height:253px;background:linear-gradient(150deg,#b0b0b0,#c1121b 45%,#e06a14 70%,#444)"></div>

<!-- partners -->
<div class="partners">
  <div class="partner"><span class="partner-sq"></span>Q WRAP</div>
  <div class="partner">GLENBRUSH</div>
  <div class="partner">DORFLINT</div>
  <div class="partner">KEBO</div>
  <div class="partner">VASTINCO</div>
</div>

<!-- contact -->
<svg class="abs" style="left:0;top:3165px" width="1200" height="720" viewBox="0 0 1200 720">
  <defs><linearGradient id="conBg" x1="0" x2="1" y1="0" y2="0.6"><stop offset="0" stop-color="#1a1b24"/><stop offset=".45" stop-color="#3a0d12"/><stop offset="1" stop-color="#c0101a"/></linearGradient></defs>
  <rect width="1200" height="720" fill="url(#conBg)"/>
</svg>
<h2 class="contact-title">CONTACT US</h2>
<p class="contact-lead">PLEASE CALL OR EMAIL TO ARRANGE A FREE ESTIMATE APPOINTMENT</p>
<div class="contact-line" style="top:3353px;width:470px">
  <svg class="icon" width="10" height="15" viewBox="0 0 10 15"><path d="M5 0a5 5 0 0 1 5 5c0 4-5 10-5 10S0 9 0 5a5 5 0 0 1 5-5z" fill="#fff"/><circle cx="5" cy="5" r="2" fill="#3a0d12"/></svg>
  <span>Harlow Trade Park, Kiln Lane, Elmbridge,<br>Westshire, WS5 2QT</span>
</div>
<div class="contact-line" style="top:3412px">
  <svg class="icon" width="13" height="13" viewBox="0 0 13 13"><path d="M3 0l2 3-1.5 1.5a8 8 0 0 0 5 5L10 8l3 2-1.5 3C5 13 0 8 0 1.5z" fill="#fff"/></svg>
  <span>07700 900384</span>
  <svg class="icon" style="margin-left:12px" width="15" height="12" viewBox="0 0 15 12"><rect width="15" height="12" fill="#fff"/><path d="M0 0l7.5 6L15 0" fill="none" stroke="#3a0d12" stroke-width="1.5"/></svg>
  <span>sales@brenvashine,co.uk</span>
</div>
<div class="field" style="left:75px;top:3465px;width:222px;height:38px">Enter Name</div>
<div class="field" style="left:315px;top:3465px;width:222px;height:38px">Phone No</div>
<div class="field" style="left:75px;top:3516px;width:462px;height:38px">Enter Email Address</div>
<div class="field message" style="left:75px;top:3567px;width:462px;height:108px">Message</div>
<div class="btn-red">SUBMIT</div>
<div class="photo map" role="img" aria-label="Street map showing the workshop location"></div>

<!-- footer wave -->
<svg class="abs" style="left:0;top:3800px" width="1200" height="120" viewBox="0 0 1200 120">
  <path d="M0 0 H1200 V30 C1050 20 950 80 700 100 C450 120 200 60 0 20 Z" fill="#a00d15"/>
  <path d="M0 20 C200 60 450 120 700 100 C950 80 1050 20 1200 30 V120 H0 Z" fill="#fff"/>
</svg>
<div class="photo footer-car" role="img" aria-label="Red sports car"></div>

<footer>
  <div class="footer-brand"><span class="brand-name">BRENVASHINE</span><span class="brand-dot"></span></div>
  <div class="footer-sub">BODYSHOP</div>
  <div class="footer-copy">Copyright ©2019 Company Name.<br>All Rights Reserved</div>
  <div class="socials"><span>Facelane</span><span>Tweeto</span><span>Snaply</span><span>Clipora</span><span>Linkora</span></div>
  <div class="footer-col" style="left:405px">
    <h4>SITE MAP</h4>Home<br>About us<br>Customisation<br>Gallery<br>Contact
  </div>
  <div class="footer-col" style="left:616px;width:200px">
    <h4>CUSTOMER SERVICES</h4>Full or part resprays<br>Dents &amp; scratch removal<br>Bumper repair<br>Alloy wheel's refurbished,<br><span style="position:relative;top:-5px">repaired &amp; painted</span>
  </div>
  <div class="badge" role="img" aria-label="Satisfaction guarantee seal"></div>
  <div class="pay"><span class="pay-sq"></span>TILLWAVE</div>
</footer>

</body>
</html>
```